Exciting & Elegant Stationary Pack

Stationary consists of
1. Letter head / Envelope
2. Business Card
3. Invoice
4. 40x40mm sticker

Attached files;

1. Logo (Other formats available on request)
2. MS word Doc - For information and description of design
3. Website image (This will be our new website so use the colours so everything ties together)
4. Sample of stationary pack we like, but feel free to be creative

Target Market(s)

Home improvement

Industry/Entity Type

Construction

Font styles to use
Other font styles liked:
• Leave up to designer - We like font used on (website attached image)

Requirements
Must have
• Please look at uploaded file of sample website and use colours
Nice to have
• Any type of business card design - eg. metal, die cut, embossed, etc...

```html
<!DOCTYPE html>
<html lang="en">
<head>
<meta charset="utf-8">
<title>Setline Tiling – Business Card</title>
<link rel="stylesheet" href="https://fonts.googleapis.com/css2?family=PT+Sans:wght@400;700&family=PT+Sans+Narrow:wght@700&display=swap">
<style>
  :root {
    --navy: #1c4268;
    --orange: #f0883a;
    --white: #ffffff;
    --backdrop: #6e6e6e;
    --social-blue: #3b5a9a;
    --social-red: #dc4a38;
    --social-dark: #333333;
  }
  * { box-sizing: border-box; margin: 0; padding: 0; }
  html, body {
    width: 1200px; height: 1163px; overflow: hidden;
    background: var(--backdrop);
    font-family: "PT Sans", Arial, sans-serif;
  }
  .canvas { position: relative; width: 1200px; height: 1163px; }
  .card {
    position: absolute; width: 716px; height: 407px; overflow: hidden;
    box-shadow: 0 8px 18px rgba(0,0,0,0.35);
  }
  .card--front { left: 105px; top: 162px; background: var(--white); }
  .card--back { left: 363px; top: 638px; background: var(--navy); }

  .brand-name {
    position: absolute; font-weight: 700; letter-spacing: 1px;
    text-transform: uppercase; line-height: 1;
  }
  .card--front .brand-name { left: 36px; top: 52px; font-size: 40px; color: var(--navy); }
  .card--back .brand-name { right: 60px; bottom: 70px; font-size: 46px; color: var(--white); }

  .connect { position: absolute; right: 58px; top: 80px; text-align: center; }
  .connect__title {
    font-family: "PT Sans Narrow", "Arial Narrow", sans-serif;
    font-size: 27px; color: var(--navy); line-height: 1;
  }
  .connect__icons { display: flex; justify-content: center; gap: 19px; margin-top: 13px; }
  .social-dot { width: 41px; height: 41px; border-radius: 50%; }
  .social-dot--one { background: var(--social-blue); }
  .social-dot--two { background: var(--social-red); }
  .social-dot--three { background: var(--social-dark); }

  .divider { position: absolute; left: 0; top: 232px; width: 100%; height: 4px; background: var(--orange); }
  .contact-band { position: absolute; left: 0; top: 236px; width: 100%; height: 171px; background: var(--navy); }

  .person { position: absolute; left: 72px; top: 62px; color: var(--white); }
  .person__name { font-size: 24px; font-weight: 700; line-height: 1.1; }
  .person__role { font-size: 16px; margin-top: 6px; }

  .contact-list {
    position: absolute; right: 48px; top: 27px; list-style: none;
    color: var(--white); font-size: 18px; text-align: right; line-height: 27px;
  }
  .contact-list li { display: flex; justify-content: flex-end; align-items: center; gap: 10px; }
  .contact-list svg { width: 16px; height: 16px; flex: none; }
  .contact-list .licence { padding-right: 26px; }

  .back-field { position: absolute; inset: 0; background: var(--navy); }
</style>
</head>
<body>
<main class="canvas">
  <section class="card card--front" aria-label="Business card front">
    <p class="brand-name">Setline Tiling</p>

    <div class="connect">
      <p class="connect__title">Connect with us</p>
      <div class="connect__icons">
        <span class="social-dot social-dot--one"></span>
        <span class="social-dot social-dot--two"></span>
        <span class="social-dot social-dot--three"></span>
      </div>
    </div>

    <div class="divider"></div>

    <div class="contact-band" role="img" aria-label="Navy tiled wall texture">
      <div class="person">
        <p class="person__name">Dara Collins</p>
        <p class="person__role">Project Manager</p>
      </div>
      <ul class="contact-list">
        <li class="licence">Lic No.,204918c</li>
        <li>0400 123 987
          <svg viewBox="0 0 16 16" aria-hidden="true"><rect x="4" y="1" width="8" height="14" rx="1.5" fill="none" stroke="#fff" stroke-width="1.5"/><rect x="7" y="12" width="2" height="1.5" fill="#fff"/></svg>
        </li>
        <li>info@setlinetiling.com.au
          <svg viewBox="0 0 16 16" aria-hidden="true"><rect x="1" y="4" width="14" height="9" fill="#fff"/><path d="M1 4 L8 9.5 L15 4" fill="none" stroke="#1c4268" stroke-width="1.2"/></svg>
        </li>
        <li>www.setlinetiling.com.au
          <svg viewBox="0 0 16 16" aria-hidden="true"><circle cx="8" cy="8" r="7" fill="#fff"/><ellipse cx="8" cy="8" rx="3" ry="7" fill="none" stroke="#1c4268" stroke-width="1"/><line x1="1" y1="8" x2="15" y2="8" stroke="#1c4268" stroke-width="1"/></svg>
        </li>
      </ul>
    </div>
  </section>

  <section class="card card--back" aria-label="Business card back">
    <div class="back-field" role="img" aria-label="Navy tiled wall texture"></div>
    <p class="brand-name">Setline Tiling</p>
  </section>
</main>
</body>
</html>
```